Recruitment of Trellan Staffing for the UK market

I want a website for the UK market to attract businesses and companies to come to us for Philipine labour. We want an information site that gives all information on what we do and how we can recruit Philippine labour.
This is a recruitment site for companies to contact us with their requirements for skilled workers coming from the Philipines over to the UK to work.

Target Market(s)

Uk Companies and businesses who want Philipine skilled workers

Industry/Entity Type

REcruitment

Coding

Number of Pages Required

5+ page

Font styles to use
Sans Serif

Colors
0054AA
0677BA
7BADD7
CADEEF
E8F1F8
0094D4
00A9DD
6FCCEA
C7EBF8
E9F6FB
EE7325
F08F49
F5BC92
FAE3D3
FDF4ED
EB3D1F
EC4F4E
F09395
F8D3D4
FCEDEE

Requirements
Must have
• Look professional and corperate with drop down menus for Home ,about, services,articles. training , contact us
Nice to have
• Look at Velmora recruitment- https://velmorarecruitment.example.co.uk/. This is my current site - https://www.trellanstaffing.example.com/
Should not have
• Cartoons or silly pictures , needs to be corperate looking

```html
<!DOCTYPE html>
<html lang="en">
<head>
<meta charset="utf-8">
<title>Trellan Staffing – Skilled Philippine Workers for UK Companies</title>
<link href="https://fonts.googleapis.com/css2?family=Roboto:ital,wght@0,400;0,500;0,700;0,900;1,700&display=swap" rel="stylesheet">
<style>
:root{
  --blue:#0054AA;--blue-mid:#0677BA;--blue-soft:#CADEEF;--blue-pale:#E8F1F8;
  --orange:#EE7325;--orange-soft:#F08F49;--red:#EB3D1F;
  --navy:#0b1b3d;--ink:#1c1c1c;--text:#444;--white:#fff;
}
*{box-sizing:border-box;margin:0;padding:0}
html,body{width:1200px;height:4212px;overflow:hidden}
body{position:relative;font-family:"Roboto",Arial,sans-serif;color:var(--text);background:var(--white)}
.abs{position:absolute}
.dots{display:flex;gap:5px}
.dots span{width:10px;height:10px;border-radius:50%;background:var(--orange)}
.dots span:nth-child(2){background:var(--orange-soft)}
.dots span:nth-child(3){background:var(--blue-soft)}
.h2{font-size:38px;font-weight:700;color:var(--ink);line-height:1.15}
.copy{font-size:15px;line-height:1.75;color:var(--text)}
.btn{display:inline-block;background:var(--blue);color:#fff;font-size:14px;font-weight:500;padding:11px 20px;border-radius:3px}
.photo{background:linear-gradient(135deg,#8a8f96,#4a5058)}
/* header */
.site-header{top:0;left:0;width:1200px;height:80px;background:#fff}
.brand{left:40px;top:20px;font-size:26px;font-weight:700;color:var(--blue);display:flex;align-items:center;gap:10px;white-space:nowrap}
.brand i{width:22px;height:22px;border-radius:50%;background:var(--red);display:block}
.nav{left:452px;top:31px;display:flex;gap:22px;font-size:13px;font-weight:500;color:var(--ink);white-space:nowrap}
.nav .active{color:var(--red)}
.phone-tab{right:0;top:0;width:272px;height:80px;background:var(--red);clip-path:polygon(28px 0,100% 0,100% 100%,0 100%);display:flex;align-items:center;justify-content:center;gap:12px;color:#fff;font-size:25px;font-weight:700;padding-left:16px;white-space:nowrap}
/* hero */
.hero{top:80px;left:0;width:1200px;height:580px;background:linear-gradient(100deg,#2a2420 0%,#6b5a4c 45%,#b9aa98 100%)}
.hero-title{left:130px;top:200px;font-size:40px;font-weight:700;color:#fff;line-height:1.2}
.hero-title em{font-style:normal;color:var(--orange)}
.hero-sub{left:130px;top:362px;font-size:15px;color:#fff;line-height:1.5;width:380px}
.hero-btn{left:130px;top:422px;background:var(--red);color:#fff;font-size:14px;font-weight:700;padding:12px 22px;border-radius:3px}
.contact-form{left:780px;top:8px;width:320px;height:492px;background:#fff;padding:30px 34px;box-shadow:0 6px 24px rgba(0,0,0,.2)}
.contact-form h3{font-size:26px;font-style:italic;font-weight:700;color:var(--ink);margin-bottom:22px}
.field{border:1px solid #d4d4d4;border-radius:3px;height:40px;font-size:13px;color:#888;padding:11px 14px;margin-bottom:14px}
.field.msg{height:90px}
.send{display:inline-block;background:#1c1c1c;color:#fff;font-size:14px;padding:12px 24px;border-radius:20px;margin-top:6px}
/* about */
.details-card{left:160px;top:730px;width:340px;border:1px solid var(--blue-soft);background:#fff}
.details-card h4{background:var(--blue);color:#fff;font-size:20px;font-weight:700;padding:14px 20px}
.details-card ul{list-style:none;padding:16px 20px 8px;font-size:13px;line-height:1.5}
.details-card li{display:flex;gap:10px;margin-bottom:10px}
.details-card li b{flex:none;width:14px;height:14px;border-radius:50%;background:var(--blue);margin-top:2px}
.socials{display:flex;gap:8px;padding:0 20px 18px}
.socials span{width:28px;height:28px;border-radius:50%;background:var(--blue)}
.about-text{left:580px;top:720px;width:470px}
.about-text .h2{font-size:31px;white-space:nowrap}
.strip{left:160px;top:1008px;width:880px;height:152px;background:linear-gradient(90deg,#4d6c96,#c8b59a,#7a8fa8,#d9c7a2,#5e7aa0)}
/* working together */
.together{left:160px;top:1310px;width:400px}
.together .red{color:var(--red);font-weight:700}
.map{left:640px;top:1250px;width:420px;height:380px;background:radial-gradient(ellipse at center,#e7e9ec 0%,#f6f7f8 60%,#fff 100%)}
/* what we do */
.wwd-frame{left:152px;top:1740px;width:320px;height:360px;background:var(--blue)}
.wwd-photo{left:180px;top:1770px;width:360px;height:390px;background:linear-gradient(135deg,#d4dde6,#6f88a6)}
.badge{left:430px;top:2030px;width:120px;height:120px;border-radius:50%;background:var(--orange);border:6px solid #fff}
.wwd-text{left:600px;top:1830px;width:440px}
/* how we help */
.help{left:160px;top:2290px;width:330px}
.help-photo{top:2300px;height:500px}
.help-cap{position:absolute;left:0;bottom:0;width:100%;height:56px;background:#fff;font-size:15px;font-weight:500;color:var(--ink);padding:18px 20px}
/* split */
.split{top:2810px;width:600px;height:410px;color:#fff;text-align:center;padding:70px 60px 0}
.split h3{font-size:34px;font-weight:700;margin-bottom:22px}
.split p{font-size:13px;line-height:1.7}
/* cards */
.cards-band{top:3220px;left:0;width:1200px;height:600px;background:var(--blue-pale)}
.card{top:3420px;width:260px;height:260px;background:#fff;text-align:center;padding:28px 22px}
.card.feature{top:3400px;height:290px;background:var(--blue);color:#fff}
.card svg{display:block;margin:0 auto 14px}
.card h5{font-size:16px;font-weight:700;color:var(--ink);margin-bottom:10px}
.card.feature h5{color:#fff}
.card p{font-size:12px;line-height:1.6;margin-bottom:16px}
.card .btn{font-size:12px;padding:9px 18px}
.card.feature .btn{background:#fff;color:var(--blue)}
/* footer */
.site-footer{top:3820px;left:0;width:1200px;height:392px;background:var(--navy);color:#cfd6e4}
.f-brand{left:160px;top:100px;font-size:24px;font-weight:700;color:#fff;display:flex;gap:10px;align-items:center}
.f-brand i{width:20px;height:20px;border-radius:50%;background:var(--red);display:block}
.f-social{left:160px;top:150px;display:flex;gap:8px}
.f-social span{width:28px;height:28px;border-radius:50%;background:var(--blue-mid)}
.f-col h6{font-size:17px;font-weight:700;color:#fff;margin-bottom:14px}
.f-col ul{list-style:none;font-size:13px;line-height:2}
.f-bottom{left:0;top:340px;width:1200px;border-top:1px solid #24375e;text-align:center;font-size:12px;padding-top:18px}
</style>
</head>
<body>

<header class="abs site-header">
  <div class="abs brand"><i></i>Trellan Staffing</div>
  <nav class="abs nav"><span class="active">HOME</span><span>ABOUT</span><span>SERVICES ▾</span><span>ARTICLES</span><span>TRAINING</span><span>CONTACT US</span></nav>
  <div class="abs phone-tab">
    <svg width="26" height="26" viewBox="0 0 24 24"><circle cx="12" cy="12" r="12" fill="#fff"/><path d="M8 6l2 0 1 3-1.5 1a7 7 0 0 0 4.5 4.5l1-1.5 3 1v2a2 2 0 0 1-2 2A10 10 0 0 1 6 8a2 2 0 0 1 2-2z" fill="#EB3D1F"/></svg>
    070 555 0142
  </div>
</header>

<section class="abs hero photo" role="img" aria-label="Team of professionals meeting around an office table">
  <h1 class="abs hero-title">Recruiting And Placing<br><em>Skilled Philippine Workers</em><br>Into UK Companies</h1>
  <p class="abs hero-sub">We source skilled workers directly from the Philippines to work in the UK.</p>
  <span class="abs hero-btn">CONTACT US →</span>
  <form class="abs contact-form">
    <h3>Contact Us Today</h3>
    <div class="field">Name</div>
    <div class="field">Email</div>
    <div class="field">Phone</div>
    <div class="field msg">Message</div>
    <span class="send">Send Message →</span>
  </form>
</section>

<aside class="abs details-card">
  <h4>Contact Details</h4>
  <ul>
    <li><b></b>12 Larkfield Gardens, Eastbourne BN20 7QX United Kingdom</li>
    <li><b></b>07700 900461</li>
    <li><b></b>sales@trellanstaffing.example.com</li>
  </ul>
  <div class="socials"><span></span><span></span><span></span><span></span></div>
</aside>
<div class="abs about-text">
  <div class="dots"><span></span><span></span><span></span></div>
  <h2 class="h2" style="margin:12px 0 16px">What The Business is About</h2>
  <p class="copy">We source skilled workers directly from the Philippines to work in the UK. With offices, training locations and specialist recruiters we can find the highest quality individuals to add value and resources to any UK business. We deliver quality based on vast experience over a number of years.</p>
</div>

<div class="abs strip" role="img" aria-label="Row of photos showing skilled Filipino workers in trades and healthcare"></div>

<div class="abs together">
  <div class="dots"><span></span><span></span><span></span></div>
  <h2 class="h2" style="margin:12px 0 16px">Working Together</h2>
  <p class="copy" style="font-size:17px">We recruit the finest talent available with our dedicated 200 strong team. Our centres are highlighted in <span class="red">Red Dots</span> on the map.</p>
  <span class="btn" style="margin-top:22px">Contact Us Today</span>
</div>
<div class="abs map" role="img" aria-label="Map of the Philippines with recruitment centres marked"></div>

<div class="abs wwd-frame"></div>
<div class="abs wwd-photo" role="img" aria-label="Recruiters reviewing candidates at a laptop"></div>
<div class="abs badge" role="img" aria-label="Twenty years of experience badge"></div>
<div class="abs wwd-text">
  <div class="dots"><span></span><span></span><span></span></div>
  <h2 class="h2" style="margin:12px 0 16px">What We Do</h2>
  <p class="copy">Our company has been established in the Philippines for over 20 years. We have mainly been recruiting Philippine workers for the off shore industry in asia but since brexit and the new rules on skilled workers entering the UK we have been working with UK companies who now have chance to recruit some of the finest hard working talent from the Philippines for their companies.</p>
</div>

<div class="abs help">
  <div class="dots"><span></span><span></span><span></span></div>
  <h2 class="h2" style="margin:12px 0 16px">How We Help</h2>
  <p class="copy">We work with companies to find skilled workers that meet the UK requirements for Visas and work permits. We guide you through the whole process and deliver highly trained people that add value to your business. We are here to help both the companies and the Philippine people to gain a better standard of living for their families.</p>
</div>
<div class="abs help-photo photo" style="left:520px;width:280px" role="img" aria-label="Engineer in hard hat with equipment"><div class="help-cap">Equipment Engineer</div></div>
<div class="abs help-photo" style="left:820px;width:228px;background:linear-gradient(135deg,#c9a46a,#6a7a8c)" role="img" aria-label="Construction workers on a building site"><div class="help-cap">Building and Construction</div></div>

<section class="abs split" style="left:0;background:var(--blue)">
  <h3>Where To Start</h3>
  <p>We need to know what your issues are and how we can understand the personnel you require, over what time frame and the number of employees you need. Once this is established we start sourcing workers in the Philippines that meet your criteria while starting the process in the UK to be able to have all the documents in place to deliver your company hard working skilled individuals.</p>
</section>
<section class="abs split" style="left:600px;background:var(--orange)">
  <h3>Contact Us Today</h3>
  <p>Please contact us today with your requirements. We can be care workers, chef, welders, steel fixers, caravan installer, masons, medical workers. The list of required skills is extensive and the Philippines workforce is equipped. Sourcing highly qualified hard working employees, contact us today and make the first step to a highly motivated, quality skilled workforce.</p>
</section>

<div class="abs cards-band"></div>
<article class="abs card" style="left:160px">
  <svg width="44" height="44" viewBox="0 0 44 44"><rect x="8" y="6" width="28" height="34" rx="3" fill="none" stroke="#0054AA" stroke-width="2.5"/><path d="M14 16h16M14 23h16M14 30h10" stroke="#0054AA" stroke-width="2.5"/></svg>
  <h5>UK Skilled Workers List</h5>
  <p>The UK government since brexit have developed a new system based on points.</p>
  <span class="btn">Read More</span>
</article>
<article class="abs card feature" style="left:470px">
  <svg width="44" height="44" viewBox="0 0 44 44"><circle cx="22" cy="16" r="8" fill="none" stroke="#fff" stroke-width="2.5"/><path d="M8 38a14 12 0 0 1 28 0" fill="none" stroke="#fff" stroke-width="2.5"/></svg>
  <h5>Sponsor Licence</h5>
  <p>If you have areas of your business that meet the entry requirements of skilled labour.</p>
  <span class="btn">Read More</span>
</article>
<article class="abs card" style="left:780px">
  <svg width="44" height="44" viewBox="0 0 44 44"><circle cx="22" cy="22" r="15" fill="none" stroke="#0054AA" stroke-width="2.5"/><path d="M22 13v10l7 4" fill="none" stroke="#0054AA" stroke-width="2.5"/></svg>
  <h5>Recruitment Timeline</h5>
  <p>Brief us on the job profiles- this is passed on to our teams in the Philippines.</p>
  <span class="btn">Read More</span>
</article>

<footer class="abs site-footer">
  <div class="abs f-brand"><i></i>Trellan Staffing</div>
  <div class="abs f-social"><span></span><span></span><span></span><span></span></div>
  <div class="abs f-col" style="left:520px;top:90px">
    <h6>Quick Links</h6>
    <ul style="display:grid;grid-template-columns:110px 110px"><li>› Home</li><li>› Articles</li><li>› About</li><li>› Training</li><li>› Services</li><li>› Contact Us</li></ul>
  </div>
  <div class="abs f-col" style="left:800px;top:90px;width:260px">
    <h6>Contact Details</h6>
    <ul><li>12 Larkfield Gardens, Eastbourne BN20 7QX United Kingdom</li><li>07700 900461</li><li>sales@trellanstaffing.example.com</li></ul>
  </div>
  <div class="abs f-bottom">© 2022 Trellan Staffing Ltd. All Rights Reserved</div>
</footer>

</body>
</html>
```